Specialised investor in e-mobility and energy wants business card design

We need a business card design that fits our existing corporate design. <The look and feel must be 'sharp'/'clean', dynamic, communicate momentum, professionalism etc (as one would imagine from a firm in the financial sector). We like the idea of a reverse-side of the card that includes the logo, and the name and contact details on the other. We expect the deliverable to be whatever format might be required to be able to get cards printed directly by a service such as kelmo press. Our website is www.zub.capital

```html
<!DOCTYPE html>
<html lang="en">
<head>
<meta charset="utf-8">
<title>ZUB Capital – Business Card</title>
<link rel="stylesheet" href="https://fonts.googleapis.com/css2?family=Lato:wght@400;700;900&family=Questrial&display=swap">
<style>
  :root {
    --forest: #324e22;
    --leaf: #86b04b;
    --paper: #ffffff;
    --stage: #2b2b2b;
    --card-w: 540px;
    --card-h: 309px;
  }
  * { margin: 0; padding: 0; box-sizing: border-box; }
  html, body {
    width: 1200px;
    height: 875px;
    overflow: hidden;
    background: var(--stage);
  }
  .sheet {
    position: relative;
    width: 1200px;
    height: 875px;
  }
  .card {
    position: absolute;
    width: var(--card-w);
    height: var(--card-h);
    overflow: hidden;
  }
  .card--logo-side {
    left: 40px;
    top: 283px;
    background: var(--forest);
    display: flex;
    align-items: center;
    justify-content: center;
  }
  .card--contact-side {
    left: 620px;
    top: 283px;
    background: var(--paper);
  }
  .card__shapes {
    position: absolute;
    inset: 0;
    width: 100%;
    height: 100%;
  }
  .brand-name {
    font-family: "Questrial", sans-serif;
    font-weight: 400;
    letter-spacing: 1px;
    display: flex;
    align-items: center;
    gap: 14px;
  }
  .brand-name__mark {
    display: inline-block;
    width: 14px;
    height: 14px;
  }
  .card--logo-side .brand-name {
    color: var(--paper);
    font-size: 58px;
  }
  .card--logo-side .brand-name__mark { background: var(--paper); }
  .card--contact-side .brand-name {
    position: absolute;
    left: 110px;
    top: 92px;
    color: var(--forest);
    font-size: 40px;
  }
  .card--contact-side .brand-name__mark { background: var(--forest); width: 11px; height: 11px; }
  .contact {
    position: absolute;
    right: 34px;
    top: 212px;
    color: var(--paper);
    font-family: "Lato", sans-serif;
    text-align: right;
  }
  .contact__name {
    font-weight: 900;
    font-size: 17px;
    letter-spacing: 0.5px;
    text-transform: uppercase;
    margin-bottom: 4px;
  }
  .contact__line {
    font-size: 10.5px;
    line-height: 15px;
  }
  .contact__line strong { font-weight: 700; }
</style>
</head>
<body>
<main class="sheet">
  <section class="card card--logo-side" aria-label="Card reverse side">
    <div class="brand-name"><span class="brand-name__mark"></span>ZUB Capital</div>
  </section>

  <section class="card card--contact-side" aria-label="Card front side">
    <svg class="card__shapes" viewBox="0 0 540 309" preserveAspectRatio="none" aria-hidden="true">
      <polygon points="0,0 540,0 0,62" fill="var(--leaf)"/>
      <polygon points="60,309 540,90 540,309" fill="var(--forest)"/>
    </svg>
    <div class="brand-name"><span class="brand-name__mark"></span>ZUB Capital</div>
    <div class="contact">
      <p class="contact__name">Lena Marvik</p>
      <p class="contact__line"><strong>ZUB Capital S.A.</strong> Geneva, Switzerland</p>
      <p class="contact__line">Ph. +41 79555 0142 E. lena@zub.capital</p>
      <p class="contact__line">www.zub.capital</p>
    </div>
  </section>
</main>
</body>
</html>
```